Verpackungen für Beutel und Dosen
Zielgruppe
PLUMAVIK.de vertreibt gesunde Lebensmittel.. erst einmal Matcha (TEE!) in 2 verschiedenen Verpackungseinheiten (100 gr.Beutel und 30gr Dose)
Zielgruppe: Veganer, Neueinst.bewusster Lebensweise, gerade auch jüngere Klientel
Aufgabenstellung
Der Einkauf als white Label muss sich schon inhaltlich an das Original des "Lieferanten" halten. Hierzu noch eine Datei. Erstmal keine BIO Abzeichen (Labels) etc..
Da es 2 verschiedene 100gr Beutel (Vor-und Rückseite) und 2 verschiedene 30 gr. Dosen sind....ist es "fast" nur ein 1 oder 2 Etiketten die zu entwerfen sind.
Ein klein wenig Platz jeweils auf der Rückseite lassen, da später noch die Logo´s BIO etc.zu integrieren sind.
2x100gr Matcha Tee (LUMO und VALOREN)
2x30gr Matcha Tee (Karvo und Beltoro)
1x200gr Matcha Latte Mix
Abmessungen:
Matcha Lumo und Valoren im 100g Beutel. Male 72 x 106 cm
Orbacant im 200g Beutel. Frontetikett: 92cm x 92 cm, Rücketikett: 72 x 106 cm
Beltoro 30g Dose sowie Karvo 30g Dose: 182 x 22 cm
Anbei noch ein Ausschnitt meiner noch offline Website (zwecks Schriftart etc.)
Unter meinem Logo bitte noch das japanische Zeichen für Matcha
抹茶
Die Schrift meiner Homepage (Shop) ist OSWALD bzw.IMPACT.
Anbei sei nun kurz noch hinzugefügt, dass ich mein "Symbol" #Ploverkind (da es schon in Kombination mit Sport stehen sollte) mit im Anhang platziert habe.
Freundliche Grüße

```html
<!DOCTYPE html>
<html lang="de">
<head>
<meta charset="utf-8">
<title>Matcha Valoren – Etikett</title>
<link rel="stylesheet" href="https://fonts.googleapis.com/css2?family=Oswald:wght@400;500;600&family=Noto+Sans+JP:wght@400&display=swap">
<style>
  :root {
    --canvas: #ffffff;
    --sky: #f3f5f2;
    --leaf-light: #9fd36a;
    --leaf-mid: #5fae3a;
    --leaf-deep: #2f7a24;
    --leaf-dark: #17451a;
    --brand-green: #2e8b4a;
    --runner-green: #6aa535;
    --band-white: rgba(245, 247, 238, 0.78);
    --title-brown: #4a2a16;
    --edge: #1c1c1c;
  }
  * { box-sizing: border-box; margin: 0; padding: 0; }
  html, body {
    width: 1200px;
    height: 851px;
    overflow: hidden;
    background: var(--canvas);
  }
  .label {
    position: absolute;
    left: 357px;
    top: 132px;
    width: 535px;
    height: 535px;
    overflow: hidden;
    box-shadow: 2px 2px 0 var(--edge);
  }
  .label__photo {
    position: absolute;
    inset: 0;
    background:
      linear-gradient(180deg,
        var(--sky) 0%,
        #e6eee0 12%,
        var(--leaf-light) 24%,
        var(--leaf-mid) 40%,
        var(--leaf-deep) 62%,
        #3f9a2e 78%,
        var(--leaf-dark) 100%);
  }
  .runner-mark {
    position: absolute;
    left: 24px;
    top: 146px;
    font-family: "Oswald", sans-serif;
    font-weight: 500;
    font-size: 15px;
    letter-spacing: 0.5px;
    color: var(--runner-green);
  }
  .brand {
    position: absolute;
    left: 190px;
    top: 28px;
    width: 160px;
    display: flex;
    flex-direction: column;
    align-items: center;
  }
  .brand__dot {
    width: 84px;
    height: 84px;
    border-radius: 50%;
    background: var(--brand-green);
  }
  .brand__name {
    margin-top: 8px;
    font-family: "Oswald", sans-serif;
    font-weight: 600;
    font-size: 21px;
    letter-spacing: 0.5px;
    color: var(--brand-green);
  }
  .title-band {
    position: absolute;
    left: 0;
    top: 283px;
    width: 100%;
    height: 157px;
    background: var(--band-white);
    display: flex;
    align-items: center;
    padding-left: 49px;
  }
  .title {
    display: flex;
    align-items: baseline;
    gap: 10px;
    color: var(--title-brown);
    white-space: nowrap;
  }
  .title__kanji {
    font-family: "Noto Sans JP", sans-serif;
    font-weight: 400;
    font-size: 44px;
  }
  .title__name {
    font-family: "Oswald", sans-serif;
    font-weight: 500;
    font-size: 50px;
    letter-spacing: -0.5px;
  }
</style>
</head>
<body>
  <main class="label">
    <div class="label__photo" role="img" aria-label="Foto: frische grüne Teeblätter einer Matcha-Plantage vor hellem Himmel"></div>

    <div class="runner-mark">#Ploverkind</div>

    <div class="brand">
      <span class="brand__dot"></span>
      <span class="brand__name">PLUMAVIK.de</span>
    </div>

    <section class="title-band">
      <h1 class="title">
        <span class="title__kanji" lang="ja">抹茶</span>
        <span class="title__name">Matcha Valoren</span>
      </h1>
    </section>
  </main>
</body>
</html>
```